FinTech company looking to revamp and expand client-facing interface for our financial models

Pellworth Engines currently has a very simple website that allows clients to interact with our financial models. We are looking to completely redesign the current site and add several extra pages to provide extra functionality. We want the design to have a modern, slick feel, that will work on both a desktop or a tablet. It should be straightforward for clients to move between different pages at any time, and clear from the layout how to interact with the more advanced features. We have included screenshots of existing pages in the attached design brief, as well as sketches of the functionality required by the new pages, but can't provide a direct link to the current site.
Target Market(s)
Professional investors that will be paying to access the interface
Industry/Entity Type
Finance
Number of Pages Required
4 page
Colors
Designer to choose colors to be used in the design.
Look and feel
Each slider illustrates characteristics of the customer's brand and the style your logo design should communicate.

```html
<!DOCTYPE html>
<html lang="en">
<head>
<meta charset="utf-8">
<title>Pellworth · ETF Pairs</title>
<link rel="stylesheet" href="https://fonts.googleapis.com/css2?family=Montserrat:wght@500;600;700&family=Roboto+Condensed:wght@400;500&family=Roboto:wght@400;500;700&display=swap">
<style>
:root{
  --frame:#e6e6e6;
  --white:#ffffff;
  --ink:#111111;
  --dark:#333333;
  --tab-active:#666666;
  --grey-head:#6a6a6a;
  --navy:#0b3566;
  --row-alt:#efefef;
  --line:#e2e2e2;
  --link:#123f7a;
}
*{box-sizing:border-box;margin:0;padding:0}
html,body{width:1200px;height:715px;overflow:hidden}
body{background:var(--frame);font-family:"Roboto",Arial,sans-serif;color:var(--ink);position:relative}
.app{position:absolute;left:14px;top:14px;width:1172px;height:687px;background:linear-gradient(#f0f0f0,#f8f8f8);overflow:hidden}
.topbar{position:absolute;left:0;top:0;width:100%;height:55px;background:var(--white);box-shadow:0 4px 10px rgba(0,0,0,.08);display:flex;font-family:"Montserrat",sans-serif;font-weight:700;font-size:13px;z-index:2}
.brand{width:166px;display:flex;align-items:center;padding-left:54px;font-size:16px}
.period{width:83px;display:flex;align-items:center;justify-content:center;border-right:1px solid var(--line)}
.period.is-active{background:var(--dark);color:var(--white);border:0}
.spacer{flex:1}
.nav-item{display:flex;align-items:center;justify-content:center;gap:8px;font-size:12.5px;border-left:1px solid var(--line)}
.nav-item svg{width:21px;height:21px}
.nav-models{width:130px;background:var(--dark);color:var(--white);border:0}
.nav-sens{width:163px}
.nav-fav{width:182px}
.content{position:absolute;left:0;top:143px;width:100%;height:544px;background:linear-gradient(#e2e2e2 0,#ececec 70px,#f7f7f7 200px,#fafafa)}
.tab{position:absolute;top:111px;height:32px;width:143px;background:var(--white);font-family:"Montserrat",sans-serif;font-weight:600;font-size:12.5px;display:flex;align-items:center;justify-content:center;border-radius:4px 4px 0 0;color:#333}
.tab.is-raised{top:102px;height:41px;align-items:flex-start;padding-top:14px}
.tab.is-active{top:92px;height:51px;background:var(--tab-active);color:var(--white);align-items:flex-start;padding-top:18px}
.tab-arrow{position:absolute;left:1084px;top:111px;width:36px;height:32px;background:var(--white);display:flex;align-items:center;justify-content:center;border-radius:4px 4px 0 0}
.tab-add{position:absolute;left:1126px;top:111px;width:37px;height:35px;background:var(--navy);display:flex;align-items:center;justify-content:center;border-radius:4px 4px 0 0}
.filter{position:absolute;top:194px;font-size:16.5px;line-height:30px;white-space:nowrap}
.filter b{font-weight:700}
.field{position:absolute;top:194px;width:166px;height:30px;background:var(--white);border:1px solid #d6d6d6;border-radius:3px;box-shadow:inset 0 1px 3px rgba(0,0,0,.12);padding:0 12px;font-size:16.5px;line-height:28px}
.export{position:absolute;top:194px;right:52px;height:30px;display:flex;align-items:center;gap:8px;color:var(--link);font-weight:700;font-size:16.5px}
.table-card{position:absolute;left:51px;top:245px;width:1071px;border-radius:6px;overflow:hidden;box-shadow:0 2px 8px rgba(0,0,0,.12);background:var(--white)}
table{border-collapse:collapse;width:100%;table-layout:fixed;font-family:"Roboto Condensed",sans-serif;font-size:16px}
th{height:65px;color:var(--white);font-family:"Montserrat",sans-serif;font-weight:600;font-size:15.5px;background:var(--grey-head);border-left:1px solid rgba(255,255,255,.2)}
th.key{background:var(--navy)}
th:first-child{border-left:0}
td{height:64.6px;padding:0 8px;border-left:1px solid var(--line);line-height:1.3}
td:first-child{border-left:0;text-align:center}
tbody tr:nth-child(even){background:var(--row-alt)}
td.time,td.quality{text-align:center}
</style>
</head>
<body>
<div class="app">
  <header class="topbar">
    <div class="brand">Pellworth</div>
    <div class="period is-active">250D</div>
    <div class="period">83D</div>
    <div class="period">42D</div>
    <div class="spacer"></div>
    <div class="nav-item nav-models">
      <svg viewBox="0 0 24 24" fill="none" stroke="#fff" stroke-width="2"><path d="M3 11 12 3l9 8"/><path d="M5 10v10h5v-6h4v6h5V10"/></svg>MODELS</div>
    <div class="nav-item nav-sens">
      <svg viewBox="0 0 24 24" fill="none" stroke="#111" stroke-width="1.6"><circle cx="12" cy="12" r="4"/><circle cx="12" cy="12" r="7.5" stroke-dasharray="2 2"/><path d="M12 1v3M12 20v3M1 12h3M20 12h3M4.2 4.2l2 2M17.8 17.8l2 2M4.2 19.8l2-2M17.8 6.2l2-2"/></svg>SENSITIVITIES</div>
    <div class="nav-item nav-fav">
      <svg viewBox="0 0 24 24" fill="none" stroke="#111" stroke-width="1.8"><path d="M12 2.5l2.9 6.1 6.6.8-4.9 4.5 1.3 6.6L12 17.2l-5.9 3.3 1.3-6.6-4.9-4.5 6.6-.8z"/></svg>FAVOURITES</div>
  </header>

  <div class="content"></div>

  <div class="tab" style="left:51px">EQUITIES</div>
  <div class="tab" style="left:199px">ETFS</div>
  <div class="tab is-raised" style="left:346px">PAIRS</div>
  <div class="tab is-active" style="left:494px">ETF PAIRS</div>
  <div class="tab is-raised" style="left:641px">FACTORS</div>
  <div class="tab" style="left:789px">NEW TAB TITLE #1</div>
  <div class="tab" style="left:937px">NEW TAB TITLE #2</div>
  <div class="tab-arrow"><svg width="14" height="18" viewBox="0 0 14 18" fill="none" stroke="#999" stroke-width="3"><path d="M4 2l7 7-7 7"/></svg></div>
  <div class="tab-add"><svg width="22" height="22" viewBox="0 0 22 22" fill="none" stroke="#fff" stroke-width="1.8"><circle cx="11" cy="11" r="9"/><path d="M11 6v10M6 11h10"/></svg></div>

  <span class="filter" style="left:53px">Quality</span>
  <span class="filter" style="left:132px"><b>Threshold:</b></span>
  <div class="field" style="left:226px">-10</div>
  <span class="filter" style="left:432px"><b>Abs.</b> Stat</span>
  <span class="filter" style="left:510px"><b>Threshold:</b></span>
  <div class="field" style="left:604px">-10</div>
  <div class="export">
    <svg width="24" height="22" viewBox="0 0 24 22" fill="none" stroke="#123f7a" stroke-width="2"><path d="M10 4H4a2 2 0 0 0-2 2v12a2 2 0 0 0 2 2h12a2 2 0 0 0 2-2v-5"/><path d="M8 14c1-5 5-8 11-8M16 2l4 4-4 4"/></svg>Export</div>

  <div class="table-card">
    <table>
      <colgroup><col style="width:92px"><col style="width:102px"><col style="width:106px"><col style="width:107px"><col span="8" style="width:83px"></colgroup>
      <thead>
        <tr><th class="key">ID ⌄</th><th class="key">Sector</th><th class="key">Time</th><th>Quality</th><th>Stat 1</th><th>Stat 2</th><th>Stat 3</th><th>Stat 4</th><th>Stat 5</th><th>Stat 6</th><th>Stat 7</th><th>Stat 8</th></tr>
      </thead>
      <tbody>
        <tr><td>Model 1</td><td>Materials</td><td class="time">2019-07-03<br>12:15:00.000</td><td class="quality">30.2288</td><td>2.01574</td><td>23.305</td><td>-0.149368</td><td>22.3054</td><td>4.63714</td><td>0.945706</td><td>2.81949</td><td>2.60858</td></tr>
        <tr><td>Model 2</td><td>Industrials</td><td class="time">2019-07-03<br>12:15:00.000</td><td class="quality">32.8694</td><td>0.87307</td><td>32.185</td><td>-0.033692</td><td>33.9911</td><td>11.5693</td><td>-0.472968</td><td>-0.830458</td><td>6.80646</td></tr>
        <tr><td>Model 3</td><td>Consumer Discretionary</td><td class="time">2019-07-03<br>12:15:00.000</td><td class="quality">1.66002</td><td>-0.569222</td><td>159.814</td><td>0.0252328</td><td>172.616</td><td>10.2875</td><td>-0.750396</td><td>-0.385309</td><td>4.69146</td></tr>
        <tr><td>Model 4</td><td>Information Technology</td><td class="time">2019-07-03<br>12:15:00.000</td><td class="quality">45.6856</td><td>0.412148</td><td>202.488</td><td>0.0084923</td><td>205.834</td><td>11.9094</td><td>-0.137913</td><td>0.449595</td><td>3.85106</td></tr>
        <tr><td>Model 5</td><td>Information Technology</td><td class="time">2019-07-03<br>12:15:00.000</td><td class="quality">75.7733</td><td>7.06728</td><td>188.605</td><td>0.016913</td><td>161.665</td><td>3.82241</td><td>0.981019</td><td>1.29847</td><td>3.34927</td></tr>
      </tbody>
    </table>
  </div>
</div>
</body>
</html>
```